Investment company needing business card

We are wanting a business card which looks sharp and easy on the eye. We are thinking of having a business card with the logo embossed on it, to really make it stand out. We will only have a small amount of information of the business card, person's name, position, email address and phone number

Contact Information for Business Card

Danielle Frost
Executive Assistant
+64 21 473 5162
danielf@harwickpartners.co.nz

Requirements
Must have
• Embossed logo
Should not have
• Not to be busy

```html
<!DOCTYPE html>
<html lang="en">
<head>
<meta charset="utf-8">
<title>Harwick Partners – Business Card</title>
<link rel="stylesheet" href="https://fonts.googleapis.com/css2?family=Source+Sans+3:wght@400;600;700&display=swap">
<style>
  :root {
    --backdrop: #d6d6d6;
    --card: #27272a;
    --brand-green: #22b573;
    --mark-grey: #5e5e60;
    --text-light: #f2f2f2;
    --divider: #4a4a4d;
  }
  * { margin: 0; padding: 0; box-sizing: border-box; }
  html, body {
    width: 1200px;
    height: 608px;
    overflow: hidden;
    background: var(--backdrop);
    font-family: "Source Sans 3", "Myriad Pro", Arial, sans-serif;
  }
  .card {
    position: absolute;
    top: 145px;
    width: 512px;
    height: 293px;
    background: var(--card);
  }
  .card--front { left: 96px; }
  .card--back { left: 616px; }

  .brand {
    position: absolute;
    display: flex;
    align-items: center;
    color: var(--brand-green);
    font-weight: 700;
    letter-spacing: 0.02em;
    white-space: nowrap;
  }
  .brand__square { background: var(--mark-grey); flex: none; }

  .card--front .brand { left: 24px; top: 274px; top: 130px; font-size: 17px; gap: 8px; }
  .card--front .brand__square { width: 32px; height: 32px; }

  .card--back .brand { left: 86px; top: 112px; font-size: 29px; gap: 14px; }
  .card--back .brand__square { width: 68px; height: 68px; }

  .divider {
    position: absolute;
    left: 257px;
    top: 91px;
    width: 1px;
    height: 110px;
    background: var(--divider);
  }
  .contact {
    position: absolute;
    left: 278px;
    top: 93px;
    color: var(--text-light);
  }
  .contact__name {
    color: var(--brand-green);
    font-weight: 700;
    font-size: 15px;
    letter-spacing: 0.02em;
    line-height: 19px;
  }
  .contact__role { font-size: 13px; line-height: 18px; margin-bottom: 8px; }
  .contact__list { list-style: none; }
  .contact__item {
    display: flex;
    align-items: center;
    gap: 6px;
    font-size: 13.5px;
    line-height: 17.5px;
  }
  .contact__icon { width: 10px; height: 10px; flex: none; fill: var(--brand-green); }
</style>
</head>
<body>
  <section class="card card--front" aria-label="Card front">
    <div class="brand">
      <span class="brand__square"></span>
      <span class="brand__name">HARWICK PARTNERS</span>
    </div>
    <div class="divider"></div>
    <div class="contact">
      <p class="contact__name">DANIELLE FROST</p>
      <p class="contact__role">Executive Assistant</p>
      <ul class="contact__list">
        <li class="contact__item">
          <svg class="contact__icon" viewBox="0 0 10 10" aria-hidden="true"><path d="M2 0.5l1.6 2.2-1 1c.6 1.3 1.5 2.2 2.8 2.8l1-1L8.6 7 8 9c-4 -.2-7.2-3.4-7.5-7.4z"/></svg>
          +64 21 473 5162
        </li>
        <li class="contact__item">
          <svg class="contact__icon" viewBox="0 0 10 10" aria-hidden="true"><path d="M0 2h10v6H0z M0.6 2.4L5 5.6 9.4 2.4" stroke="#27272a" stroke-width="0.8"/></svg>
          danielf@harwickpartners.co.nz
        </li>
        <li class="contact__item">
          <svg class="contact__icon" viewBox="0 0 10 10" aria-hidden="true"><circle cx="5" cy="5" r="4.6"/><path d="M0.5 5h9M5 0.5v9M5 0.5c-2.4 2.6-2.4 6.4 0 9M5 0.5c2.4 2.6 2.4 6.4 0 9" fill="none" stroke="#27272a" stroke-width="0.6"/></svg>
          www.harwickpartners.co.nz
        </li>
      </ul>
    </div>
  </section>

  <section class="card card--back" aria-label="Card back">
    <div class="brand">
      <span class="brand__square"></span>
      <span class="brand__name">HARWICK PARTNERS</span>
    </div>
  </section>
</body>
</html>
```